RW Holloway LLC Business Card - Civil Engineering & Consulting Firm

We need a Business Card that is elegant, and masculine.  It is our Professional Civil Engineering & Consulting Company located in San Antonio TX (Not s construction or builder firm- no gears & no tool images please). We provide civil engineering services including  commercial site plans, grading and drainage plans, utility plans, hydraulics and hydrology, land planning, utility coordination, and other general civil engineering services related to commercial and residential development.
We have 2 existing Logos. We would like to convey reliability, strength, trustworthiness and attention to detail.  Blues and orange tones as per logo We are OK with the use of a darker blue in the mix.  We have 2 logo versions - Full Company Name Logo to go on the back of card, & Small Icon Logo for the front w/ personal Info.

Target Market(s)
Architects, Real Estate Developers, Other Strctural Engineers, Surveyers, General Contractors
Industry/Entity Type
Professional Civil Engineering
Contact Information for Business Card
Name, Position, Address, Cell & Office #, email, and company website
Font styles to use
Other font styles liked:
- Avian
Requirements
Should not have
- No Tools, No Gears, no Cranes, or Construction Equipment.

```html
<!DOCTYPE html>
<html lang="en">
<head>
<meta charset="utf-8">
<title>RW Holloway LLC Business Card</title>
<link rel="stylesheet" href="https://fonts.googleapis.com/css2?family=Montserrat:wght@400;500;700&family=Josefin+Sans:wght@400&display=swap">
<style>
  :root {
    --page: #3b3b3b;
    --card: #1a1a1b;
    --blue: #6fa3d8;
    --orange: #e8902a;
    --white: #f1f1f1;
    --grey: #bdbdbd;
  }
  * { margin: 0; padding: 0; box-sizing: border-box; }
  html, body { width: 1200px; height: 801px; overflow: hidden; }
  body {
    background: radial-gradient(ellipse at 50% 40%, #474747, var(--page));
    font-family: "Montserrat", sans-serif;
    position: relative;
  }
  .card {
    position: absolute;
    top: 246px;
    width: 540px;
    height: 309px;
    background: var(--card);
    border-right: 2px solid var(--blue);
    border-bottom: 2px solid var(--blue);
    box-shadow: 0 14px 30px rgba(0,0,0,.45);
    overflow: hidden;
  }
  .card--front { left: 40px; }
  .card--back { left: 620px; }

  .wordmark {
    font-family: "Josefin Sans", sans-serif;
    font-weight: 400;
    color: var(--blue);
    letter-spacing: 3px;
    white-space: nowrap;
  }
  .tagline {
    font-family: "Josefin Sans", sans-serif;
    color: var(--orange);
    letter-spacing: 5px;
    text-transform: uppercase;
    white-space: nowrap;
  }
  .rule { height: 1px; background: var(--blue); }

  /* front */
  .front-brand { position: absolute; left: 34px; top: 132px; }
  .front-brand .wordmark { font-size: 25px; }
  .front-brand .rule { width: 230px; margin: 6px 0 6px; }
  .front-brand .tagline { font-size: 9px; letter-spacing: 3.6px; }
  .divider { position: absolute; left: 292px; top: 40px; width: 1px; height: 230px; background: var(--blue); }
  .contact { position: absolute; left: 316px; top: 52px; color: var(--white); }
  .contact__name { color: var(--blue); font-weight: 700; font-size: 17px; letter-spacing: .5px; text-transform: uppercase; }
  .contact__title { font-size: 12px; margin: 2px 0 14px; }
  .contact__address { font-size: 12px; line-height: 1.45; margin-bottom: 14px; }
  .contact__list { list-style: none; font-size: 11.5px; line-height: 1.7; }
  .contact__list li { display: flex; align-items: center; gap: 7px; }
  .contact__list svg { width: 10px; height: 10px; flex: none; }

  /* back */
  .back-band {
    position: absolute; left: 0; top: 0; width: 170px; height: 100%;
    background: linear-gradient(160deg, #111 0%, #2a2a2a 45%, #8a8a8a 100%);
  }
  .back-brand { position: absolute; left: 210px; top: 110px; }
  .back-brand .wordmark { font-size: 34px; }
  .back-brand .rule { width: 300px; margin: 8px 0 8px; }
  .back-brand .tagline { font-size: 11px; letter-spacing: 4.4px; }
</style>
</head>
<body>

<section class="card card--front" aria-label="Card front">
  <div class="front-brand">
    <div class="wordmark">RW Holloway LLC</div>
    <div class="rule"></div>
    <div class="tagline">Consulting Engineers</div>
  </div>
  <div class="divider"></div>
  <div class="contact">
    <div class="contact__name">Dale Brennan</div>
    <div class="contact__title">President</div>
    <div class="contact__address">4150 Westover Hills<br>San Antonio TX 78251</div>
    <ul class="contact__list">
      <li><svg viewBox="0 0 10 10"><rect x="2" y="0.5" width="6" height="9" rx="1" fill="none" stroke="var(--orange)" stroke-width="1.2"/></svg>210-555-0147</li>
      <li><svg viewBox="0 0 10 10"><path d="M2 1l2 0 1 2.5-1.3 1a6 6 0 0 0 2.8 2.8l1-1.3L10 7v2a1 1 0 0 1-1 1A9 9 0 0 1 0 2a1 1 0 0 1 1-1z" fill="var(--orange)"/></svg>210-555-0148</li>
      <li><svg viewBox="0 0 10 10"><rect x="0.5" y="2" width="9" height="6" fill="var(--orange)"/><path d="M0.5 2l4.5 3.5L9.5 2" fill="none" stroke="var(--card)" stroke-width="1"/></svg>info@rwhollowayconsulting.com</li>
      <li><svg viewBox="0 0 10 10"><circle cx="5" cy="5" r="4.5" fill="var(--orange)"/><path d="M0.5 5h9M5 0.5c-2.5 3-2.5 6 0 9M5 0.5c2.5 3 2.5 6 0 9" fill="none" stroke="var(--card)" stroke-width=".8"/></svg>www.rwhollowayconsulting.com</li>
    </ul>
  </div>
</section>

<section class="card card--back" aria-label="Card back">
  <div class="back-band" role="img" aria-label="Large decorative company mark in silver gradient"></div>
  <div class="back-brand">
    <div class="wordmark">RW Holloway LLC</div>
    <div class="rule"></div>
    <div class="tagline">Consulting Engineers</div>
  </div>
</section>

</body>
</html>
```